Halvik - consultancy website

I need a new design for my webpage/presence [to be functioning with Wordpress - I have a programmer to set it up but not the design idea].
My company is Halvik - a consultancy firm focused on growth management for Swedish SME's primarily;. We call it Leadership toolkit for firms on the rise, kind of a doctor helping small become big. Contentwise, its a simple frontpage + 3-4 subpages with content re company/myself/focus etc. The new site should communicate a fresh, trustworthy take yet simple and functional on all devices [i.e. think UI compatible for mobile/tablet]. Current building parts/form elements are
a) existing logo and text elements
b) existing pictures
c) the yellowish color
colours and new ideas on pictures/positioning are welcome. I prefer a 'full width page' solution with centralised text elements but that's all up to you to suggest. Current site is a quickfix made by myself - now I'm moving it to a new platform so want to take the opportunity to make it
Nothing superspecial as it is a 2-man show; on the other hand I still want to have a modern & fresh reflection of my brand in digital environments. Help me out!
www.halvik-demo.se
Best
Lina Bergqvist

```html
<!DOCTYPE html>
<html lang="en">
<head>
<meta charset="utf-8">
<title>Halvik – Growth Management</title>
<link href="https://fonts.googleapis.com/css2?family=Montserrat:wght@700&family=Open+Sans:wght@400;600;700&display=swap" rel="stylesheet">
<style>
:root{
  --green:#6aab3a;
  --orange:#f3a834;
  --peach:#fcefe4;
  --ink:#2a2a2a;
  --dark:#262626;
  --text:#555;
  --white:#fff;
}
*{box-sizing:border-box;margin:0;padding:0}
html,body{width:1200px;height:2280px;overflow:hidden}
body{font-family:"Open Sans",Arial,sans-serif;color:var(--text);background:var(--white);position:relative}
.btn{display:inline-block;background:var(--green);color:var(--white);font-size:11px;font-weight:700;letter-spacing:.5px;text-transform:uppercase;padding:10px 22px;border-radius:2px}
.btn--dark{background:var(--dark)}

/* header */
.site-header{position:absolute;top:0;left:0;width:1200px;height:152px}
.brand{position:absolute;left:40px;top:22px}
.brand__name{font-family:"Open Sans",Arial,sans-serif;font-weight:400;font-size:54px;color:var(--ink);line-height:1;letter-spacing:-1px}
.brand__tagline{font-size:15px;font-weight:700;color:var(--ink);margin-top:12px}
.contact{position:absolute;top:46px;display:flex;gap:10px;font-size:12px;line-height:17px;color:#777}
.contact svg{flex:none;margin-top:2px}
.contact--address{left:490px}
.contact--phone{left:720px}
.site-header .btn{position:absolute;right:40px;top:44px;padding:11px 20px}

/* nav */
.main-nav{position:absolute;top:152px;left:120px;width:1040px;height:40px;background:var(--dark);display:flex;align-items:center}
.main-nav a{color:#ddd;font-size:13px;padding:0 30px;height:40px;line-height:40px;text-decoration:none}
.main-nav a.is-active{background:var(--green);color:var(--white)}
.search{margin-left:auto;margin-right:12px;width:250px;height:26px;background:var(--white);display:flex;align-items:center;justify-content:space-between;padding:0 8px;font-size:11px;color:#aaa}

/* hero */
.hero{position:absolute;top:192px;left:0;width:1200px;height:520px;
  background:
    radial-gradient(ellipse 420px 300px at 330px 200px,rgba(235,238,241,.55),rgba(235,238,241,0) 70%),
    radial-gradient(ellipse 380px 260px at 200px 470px,rgba(30,32,36,.7),rgba(30,32,36,0) 70%),
    linear-gradient(100deg,#3c4046 0%,#8d949b 35%,#d9dcdf 62%,#e4e6e8 78%,#b9bec3 100%)}
.hero__caption{position:absolute;left:740px;top:210px}
.hero__title{font-family:"Montserrat",Arial,sans-serif;font-weight:700;font-size:42px;color:var(--green);line-height:1.1}
.hero__sub{font-family:"Montserrat",Arial,sans-serif;font-weight:700;font-size:28px;color:var(--ink);margin-top:8px;padding-left:120px}
.hero__dots{position:absolute;right:40px;bottom:40px;display:flex;gap:8px}
.hero__dots span{width:12px;height:12px;border-radius:50%;background:var(--ink)}
.hero__dots span:first-child{background:var(--white)}

/* what we do */
.what{position:absolute;top:712px;left:0;width:1200px;height:348px;background:var(--orange)}
.what__photo{position:absolute;left:0;top:0;width:470px;height:348px;background:linear-gradient(160deg,#f4f2ee,#d9cfc3 60%,#8a6a52)}
.what__body{position:absolute;left:520px;top:40px;width:630px;color:var(--white)}
.section-title{font-size:34px;font-weight:400;line-height:1.1}
.what__text{font-size:11px;line-height:17px;margin:14px 0}
.checklist{list-style:none;display:grid;grid-template-columns:1fr 1fr;gap:8px 40px;font-size:11px;margin-bottom:22px}
.checklist li{display:flex;align-items:center;gap:8px}
.checklist li::before{content:"";width:9px;height:9px;background:var(--white)}

/* who we are */
.who{position:absolute;top:1060px;left:0;width:1200px;height:580px;background:var(--peach)}
.who__body{position:absolute;left:40px;top:56px;width:690px}
.who .section-title{color:var(--ink);font-size:40px}
.who__lead{color:var(--orange);font-size:13px;margin:10px 0 16px}
.who__text{font-size:11px;line-height:18px;margin-bottom:20px}
.who__photo{position:absolute;right:0;top:0;width:370px;height:580px;background:linear-gradient(180deg,#f3f1ee,#e2ddd6 55%,#2d2d2d 85%)}
.quote{position:absolute;left:40px;top:436px;width:740px;border:1px solid #e2d2c3;background:var(--white);padding:20px 28px;font-size:11px;line-height:18px;color:#666}
.quote__by{display:block;text-align:right;margin-top:8px;color:var(--orange);font-size:10px}

/* why we */
.why{position:absolute;top:1640px;left:0;width:1200px;height:320px;background:var(--green)}
.why__photo{position:absolute;left:0;top:0;width:520px;height:320px;background:linear-gradient(135deg,#c9b08d,#e6dccf 50%,#8e7a63)}
.why__body{position:absolute;left:570px;top:34px;width:590px;color:var(--white)}
.why__lead{font-size:13px;margin:8px 0 14px}
.why__text{font-size:11px;line-height:17px;margin-bottom:12px}

/* footer */
.site-footer{position:absolute;top:1960px;left:0;width:1200px;height:320px;background:var(--dark);color:#bbb}
.site-footer .brand__name{color:var(--white);font-size:46px}
.footer__brand{position:absolute;left:40px;top:40px;width:340px}
.footer__brand p{font-size:11px;line-height:16px;margin-top:14px}
.footer__copy{font-size:10px;margin-top:12px;color:#888}
.footer__col{position:absolute;top:50px}
.footer__col h3{color:var(--white);font-size:17px;font-weight:600;margin-bottom:16px}
.footer__col--touch{left:540px}
.field{width:200px;height:28px;background:var(--white);font-size:10px;color:#999;padding:7px 10px;margin-bottom:10px}
.footer__col--social{left:870px}
.social{display:flex;gap:10px}
.social span{width:32px;height:32px;border:2px solid #ccc}
</style>
</head>
<body>

<header class="site-header">
  <div class="brand">
    <div class="brand__name">Halvik</div>
    <div class="brand__tagline">Leadership toolkit for firms on the rise</div>
  </div>
  <div class="contact contact--address">
    <svg width="14" height="18" viewBox="0 0 14 18"><path d="M7 0a7 7 0 0 0-7 7c0 5 7 11 7 11s7-6 7-11a7 7 0 0 0-7-7zm0 10a3 3 0 1 1 0-6 3 3 0 0 1 0 6z" fill="#999"/></svg>
    <div>1990 Halvik Company<br>Norra Gatan 12, 114 32 Stockholm</div>
  </div>
  <div class="contact contact--phone">
    <svg width="16" height="16" viewBox="0 0 16 16"><path d="M3 1l3 3-2 2a10 10 0 0 0 6 6l2-2 3 3-2 2C7 15 1 9 1 3z" fill="#999"/></svg>
    <div>+46 (0) 700 00 00 00<br>info@halvik-demo.se</div>
  </div>
  <span class="btn">Need a consultation</span>
</header>

<nav class="main-nav">
  <a class="is-active">Home</a>
  <a>What we do</a>
  <a>Who we are</a>
  <a>Why we</a>
  <div class="search"><span>Search</span>
    <svg width="12" height="12" viewBox="0 0 12 12"><circle cx="5" cy="5" r="4" fill="none" stroke="#999" stroke-width="1.5"/><path d="M8 8l3.5 3.5" stroke="#999" stroke-width="1.5"/></svg>
  </div>
</nav>

<section class="hero" role="img" aria-label="Businessman in a dark suit drawing a rising growth chart on a glass board">
  <div class="hero__caption">
    <div class="hero__title">Growth Management</div>
    <div class="hero__sub">for Swedish SME's...</div>
  </div>
  <div class="hero__dots"><span></span><span></span></div>
</section>

<section class="what">
  <div class="what__photo" role="img" aria-label="Smiling woman with curly hair"></div>
  <div class="what__body">
    <h2 class="section-title">What We Do</h2>
    <p class="what__text">Halvik helps owners and leaders of growing firms take the next step. We act as a partner through change, bringing structure, clarity and tools that make growth manageable. Whether you are scaling up, restructuring or building a stronger team, we work close to you to turn ambition into a working plan and daily routine. When you need it.</p>
    <ul class="checklist">
      <li>Growth management</li>
      <li>Interim leadership support</li>
      <li>Business development</li>
      <li>Project management</li>
      <li>Organisational development</li>
      <li>Consulting services</li>
    </ul>
    <span class="btn">Click here more</span>
  </div>
</section>

<section class="who">
  <div class="who__body">
    <h2 class="section-title">Who We Are?</h2>
    <p class="who__lead">Growth Enabler</p>
    <p class="who__text">Independent consulting across several industries, supporting businesses influenced by a fast forward mindset and driven to optimise operations while bringing long-term stability and innovation. Our team has over 20 years in the leading organisations relevant to small and medium business. Several managing roles in global operations and Nordic business transformation have set us up with a broad range of competencies and a true global profile.</p>
    <span class="btn btn--dark">Click here more</span>
  </div>
  <div class="who__photo" role="img" aria-label="Portrait of Lina Bergqvist with arms crossed"></div>
  <blockquote class="quote">
    Improved operations come from responsibility and a commitment to take the smallest of steps towards sustainable growth, together with clear priorities, strong leadership and a culture that keeps every person focused on market development.
    <span class="quote__by">— Lina Bergqvist, Halvik</span>
  </blockquote>
</section>

<section class="why">
  <div class="why__photo" role="img" aria-label="Person resting head on a table covered with food and drinks"></div>
  <div class="why__body">
    <h2 class="section-title">Why We</h2>
    <p class="why__lead">You got your act together? Congratulations.</p>
    <p class="why__text">Growing small businesses often face unclear roles, overloaded leaders and processes that cannot keep up. We help you find the right focus, the right structure and the right people, so growth becomes a strength rather than a burden on your company.</p>
    <p class="why__text">A growth journey needs an experienced guide. We give you steady support and proven methods so the whole team moves forward with confidence.</p>
    <span class="btn btn--dark">Click here more</span>
  </div>
</section>

<footer class="site-footer">
  <div class="footer__brand">
    <div class="brand__name">Halvik</div>
    <p>Leadership toolkit for firms on the rise. You want to grow, we help you get there step by step.</p>
    <p class="footer__copy">Copyright © Halvik. All rights reserved.</p>
  </div>
  <div class="footer__col footer__col--touch">
    <h3>Get in touch!</h3>
    <div class="field">Enter your email</div>
    <span class="btn">Subscribe</span>
  </div>
  <div class="footer__col footer__col--social">
    <h3>Follow With Us</h3>
    <div class="social"><span></span><span></span><span></span><span></span></div>
  </div>
</footer>

</body>
</html>
```